real esate business card with company logo and name

we need a business card design for a real esate company

The company name is Walsh & Brand Pty Ltd, and we have our logo designed and will upload. We want classic or moden feel. Black or white background. looks more textured. Should include folowinginformations
Owen Walsh and Lucy Brand
Sales Agents & Onsite Manager
p: 07 5948 2063
F: 07 5948 2174
M:0431 857 219
3/42 Marlow Crescent, FERNLEA QLD 4213

We want this business card looks professonal. Thank you in advance.

Industry/Entity Type

Real Estate Agent

Contact Information for Business Card

Owen Walsh and Lucy Brand
Onsite Manager & Sales Agents
p: 07 5948 2063
M:0431 857 219

Font styles to use
Serif

Colors
000000
fbfbfb
333333
959595

Requirements
Must have
• company logo and name, black or white back ground

```html
<!DOCTYPE html>
<html lang="en">
<head>
<meta charset="utf-8">
<title>Walsh &amp; Brand Pty Ltd – Business Card</title>
<link rel="stylesheet" href="https://fonts.googleapis.com/css2?family=Oswald:wght@300;400&family=Source+Sans+3:wght@400&display=swap">
<style>
  :root {
    --backdrop: #e4e4e4;
    --card-black: #111213;
    --card-white: #f7f7f7;
    --band-dark: #4d5057;
    --band-light: #c4c4c6;
    --ink-mid: #555659;
    --brand-grey: #8c8c8e;
    --mark-grey: #6e6f73;
    --icon-grey: #a3a3a6;
  }
  html, body {
    margin: 0;
    width: 1200px;
    height: 1200px;
    overflow: hidden;
    background: var(--backdrop);
  }
  .canvas {
    position: relative;
    width: 1200px;
    height: 1200px;
  }
  .card {
    position: absolute;
    width: 711px;
    height: 418px;
    border-radius: 28px;
    overflow: hidden;
  }
  .card-front {
    left: 238px;
    top: 118px;
    background: var(--card-black);
  }
  .card-back {
    left: 231px;
    top: 644px;
    background: var(--card-white);
  }
  .brand-square {
    position: absolute;
    width: 140px;
    height: 140px;
    background: var(--mark-grey);
  }
  .card-front .brand-square {
    left: 285px;
    top: 115px;
  }
  .card-back .brand-square {
    left: 496px;
    top: 183px;
  }
  .brand-name {
    position: absolute;
    font-family: "Oswald", sans-serif;
    font-weight: 300;
    letter-spacing: 0.5px;
    color: var(--brand-grey);
    white-space: nowrap;
    margin: 0;
  }
  .card-front .brand-name {
    left: 0;
    right: 0;
    top: 285px;
    text-align: center;
    font-size: 22px;
  }
  .card-back .brand-name {
    left: 468px;
    top: 357px;
    font-size: 21px;
  }
  .wave {
    position: absolute;
    left: 0;
    top: 0;
  }
  .people {
    position: absolute;
    left: 47px;
    top: 117px;
    margin: 0;
    font-family: "Oswald", sans-serif;
    font-weight: 400;
    font-size: 24px;
    color: var(--ink-mid);
  }
  .role {
    position: absolute;
    left: 47px;
    top: 158px;
    margin: 0;
    font-family: "Source Sans 3", sans-serif;
    font-size: 14px;
    color: var(--ink-mid);
  }
  .contacts {
    position: absolute;
    left: 47px;
    top: 246px;
    margin: 0;
    padding: 0;
    list-style: none;
    font-family: "Source Sans 3", sans-serif;
    font-size: 17px;
    color: var(--ink-mid);
  }
  .contacts li {
    display: flex;
    align-items: center;
    height: 26.5px;
  }
  .contacts svg {
    width: 16px;
    height: 16px;
    margin-right: 18px;
    fill: var(--icon-grey);
  }
  .address {
    position: absolute;
    left: 47px;
    top: 330px;
    margin: 0;
    font-family: "Source Sans 3", sans-serif;
    font-style: normal;
    font-size: 17px;
    line-height: 27px;
    color: var(--ink-mid);
  }
</style>
</head>
<body>
<main class="canvas">

  <section class="card card-front" aria-label="Card front">
    <div class="brand-square" aria-hidden="true"></div>
    <p class="brand-name">WALSH &amp; BRAND PTY LTD.</p>
  </section>

  <section class="card card-back" aria-label="Card back">
    <svg class="wave" width="711" height="418" viewBox="0 0 711 418" aria-hidden="true">
      <path d="M0,0 H711 V150 C610,140 520,55 390,48 C260,42 110,50 0,52 Z" fill="var(--band-light)"/>
      <path d="M0,0 H711 V132 C610,122 520,38 390,30 C260,24 110,28 0,32 Z" fill="var(--band-dark)"/>
      <path d="M80,62 C200,50 330,48 430,60 C540,75 620,130 711,152 C620,138 540,92 430,74 C320,58 200,56 80,62 Z" fill="var(--band-light)"/>
    </svg>

    <h1 class="people">Owen Walsh &amp; Lucy Brand</h1>
    <p class="role">Sales Agents &amp; Onsite Manager</p>

    <ul class="contacts">
      <li>
        <svg viewBox="0 0 16 16" aria-label="Mobile"><path d="M4 0h8a1 1 0 0 1 1 1v14a1 1 0 0 1-1 1H4a1 1 0 0 1-1-1V1a1 1 0 0 1 1-1zm1 2v10h6V2zm3 11a1 1 0 1 0 0 2 1 1 0 0 0 0-2z"/></svg>
        0431 857 219
      </li>
      <li>
        <svg viewBox="0 0 16 16" aria-label="Phone"><path d="M1 5c0-2 3-3 7-3s7 1 7 3v1h-4V4.5H5V6H1zM3 8h10l1 6H2zm5 1.5a2 2 0 1 0 0 4 2 2 0 0 0 0-4z"/></svg>
        07 5948 2063
      </li>
      <li>
        <svg viewBox="0 0 16 16" aria-label="Fax"><path d="M4 1h8v4H4zM1 6h14v7h-3v2H4v-2H1zm4 5v3h6v-3z"/></svg>
        07 5948 2174
      </li>
    </ul>

    <address class="address">3/42 Marlow Crescent,<br>FERNLEA QLD 4213</address>

    <div class="brand-square" aria-hidden="true"></div>
    <p class="brand-name">WALSH &amp; BRAND PTY LTD.</p>
  </section>

</main>
</body>
</html>
```